Design concept Visual UI of future mobile app - healthcare

Hi,
I'm looking for a top designer, innovative with strong experience in user interface

The app will be connected to a future health website related to depression and addiction by helping the user to track the moods, tired, anxiety using this mobile app.

I attached the deck of the overall project but I can send you a specific presentation for the app only

thanks

Target Market(s)

Switzerland, UK, Germany and France

Industry/Entity Type

Mental Health

Logo Text

Health, hope

Font styles to use
Sans Serif

Colors
cee9f5
33a6d7
0692cd
0255a3
3276b5
85abd2

Requirements
Must have
• keep it simple, easy to navigate
• The user should be able to track the moods on a daily basis,
• sleep time, and rate how the feel on the day
• To be able to get information from the sync deck of vexlo
Nice to have
• to be able share this app with a friend

```html
<!DOCTYPE html>
<html lang="en">
<head>
<meta charset="utf-8">
<title>Mood Tracker – App Screens</title>
<link rel="stylesheet" href="https://fonts.googleapis.com/css2?family=Open+Sans:wght@400;600;700&display=swap">
<style>
  :root {
    --page: #f2f2f2;
    --sky-top: #2a86cb;
    --sky-mid: #3b9ad8;
    --sky-low: #62b3e6;
    --band: rgba(2, 85, 163, 0.35);
    --header: rgba(2, 85, 163, 0.18);
    --text: #ffffff;
    --text-soft: #cee9f5;
    --date: #0255a3;
    --status-dark: #111111;
    --status-light: #ffffff;
    --chart-hot: #e8461c;
    --chart-warm: #f08a1e;
    --chart-mid: #b59a2a;
    --chart-cool: #6f8f2b;
    --chart-base: #5c7f2a;
  }
  * { box-sizing: border-box; margin: 0; padding: 0; }
  html, body { width: 1200px; height: 800px; overflow: hidden; }
  body {
    background: var(--page);
    font-family: "Open Sans", Arial, sans-serif;
    color: var(--text);
    position: relative;
  }
  .screen {
    position: absolute;
    width: 190px;
    height: 334px;
    overflow: hidden;
    background: linear-gradient(180deg, var(--sky-top) 0%, var(--sky-mid) 55%, var(--sky-low) 100%);
  }
  .screen--graphs { left: 233px; top: 228px; }
  .screen--profile { left: 510px; top: 229px; }
  .screen--activity { left: 786px; top: 228px; }

  .sky-clouds {
    position: absolute; left: 0; right: 0; bottom: 0; height: 90px;
    background: linear-gradient(180deg, rgba(255,255,255,0) 0%, rgba(230,244,252,0.35) 100%);
  }

  .status-bar {
    position: relative; height: 12px;
    display: flex; align-items: center; justify-content: space-between;
    padding: 0 4px; font-size: 5px;
    background: var(--status-dark); color: var(--status-light);
  }
  .status-bar--light { background: var(--status-light); color: #111; }
  .status-bar .battery { display: inline-block; width: 10px; height: 4px; background: currentColor; border-radius: 1px; vertical-align: middle; margin-left: 2px; }

  .app-header {
    position: relative; height: 22px; margin-top: 8px;
    display: flex; align-items: center; justify-content: center;
    background: var(--header);
    font-size: 8.5px; font-weight: 700; letter-spacing: 0.1px; text-transform: uppercase;
  }
  .app-header .menu { position: absolute; left: 20px; top: 7px; width: 10px; height: 8px;
    border-top: 1.5px solid #fff; border-bottom: 1.5px solid #fff; }
  .app-header .menu::after { content: ""; position: absolute; left: 0; right: 0; top: 1.7px; border-top: 1.5px solid #fff; }
  .app-header .prev, .app-header .next { position: absolute; top: 4px; font-weight: 400; font-size: 11px; }
  .screen--graphs .prev { left: 38px; } .screen--graphs .next { right: 20px; }
  .screen--profile .prev { left: 36px; } .screen--profile .next { right: 24px; }
  .screen--activity .prev { left: 38px; } .screen--activity .next { right: 20px; }
  .app-header .edit-icon { width: 8px; height: 7px; border: 1px solid #fff; margin-right: 3px; }

  /* Tracking graphs */
  .period-label { position: absolute; width: 100%; text-align: center; font-size: 5.5px; font-weight: 700; line-height: 6px; }
  .chart { position: absolute; }
  .chart-fill { position: absolute; inset: 0;
    background: linear-gradient(180deg, var(--chart-hot) 0%, var(--chart-warm) 25%, var(--chart-mid) 50%, var(--chart-cool) 75%, var(--chart-base) 100%); }
  .chart svg { position: absolute; inset: 0; }
  .axis-months { position: absolute; display: flex; justify-content: space-between; font-size: 3.8px; color: var(--text-soft); }
  .axis-years { position: absolute; font-size: 3.8px; color: var(--text-soft); line-height: 8px; }

  /* Profile */
  .profile-name { position: absolute; top: 45px; width: 100%; text-align: center; font-size: 8px; color: var(--text-soft); }
  .profile-photo { position: absolute; left: 40px; top: 61px; width: 42px; height: 50px; border-radius: 4px;
    background: linear-gradient(160deg, #c9a27a, #e9c9ad 60%, #a98866); border: 1px solid rgba(255,255,255,0.6); }
  .profile-facts { position: absolute; left: 94px; top: 63px; font-size: 7.5px; line-height: 13px; }
  .profile-facts b { font-weight: 700; }
  .link-list { position: absolute; left: 24px; top: 119px; font-size: 7.5px; line-height: 13px; list-style: none; }
  .link-list li::before { content: ""; display: inline-block; width: 6px; height: 6px; background: #fff; border-radius: 1px; margin-right: 4px; vertical-align: -0.5px; }
  .link-list li::after { content: " >"; margin-left: 3px; }
  .section-band { position: absolute; left: 0; right: 0; height: 17px; background: var(--band);
    font-size: 7.5px; padding-left: 21px; line-height: 17px; }
  .people-list { position: absolute; left: 23px; font-size: 7.5px; line-height: 13px; list-style: none; }
  .people-list li::before { content: ""; display: inline-block; width: 5px; height: 6px; background: #fff; border-radius: 3px 3px 1px 1px; margin-right: 5px; vertical-align: -0.5px; }
  .people-list li.add::before { width: 6px; height: 6px; border-radius: 50%; }
  .plain-list { position: absolute; left: 33px; font-size: 7.5px; line-height: 13px; list-style: none; }

  /* Activity */
  .activity-feed { position: absolute; left: 17px; right: 12px; top: 43px; }
  .activity-title { font-size: 8px; line-height: 11px; font-weight: 400; }
  .activity-text { font-size: 5px; line-height: 7.5px; color: var(--text-soft); margin-top: 2px; }
  .activity-tips { list-style: none; font-size: 5px; line-height: 7.5px; color: var(--text-soft); margin-top: 2px; }
  .activity-tips li { padding-left: 6px; }
  .activity-tips li::before { content: "•"; margin-right: 3px; margin-left: -3px; }
  .activity-date { font-size: 5px; color: var(--date); margin: 3px 0 4px; }
</style>
</head>
<body>

<!-- Tracking graphs -->
<section class="screen screen--graphs">
  <div class="status-bar"><span>●●●○○ NOVA</span><span>4:21 PM</span><span>100%<i class="battery"></i></span></div>
  <header class="app-header"><span class="menu"></span><span class="prev">&lt;</span>Tracking Graphs<span class="next">&gt;</span></header>

  <div class="period-label" style="top:52px">MONTH<br>2015</div>
  <div class="chart" style="left:16px;top:70px;width:154px;height:109px">
    <div class="chart-fill"></div>
    <svg viewBox="0 0 154 109" width="154" height="109">
      <g stroke="rgba(255,255,255,0.45)" stroke-width="0.5">
        <line x1="13" y1="0" x2="13" y2="109"/><line x1="26" y1="0" x2="26" y2="109"/><line x1="39" y1="0" x2="39" y2="109"/>
        <line x1="51" y1="0" x2="51" y2="109"/><line x1="64" y1="0" x2="64" y2="109"/><line x1="77" y1="0" x2="77" y2="109"/>
        <line x1="90" y1="0" x2="90" y2="109"/><line x1="103" y1="0" x2="103" y2="109"/><line x1="116" y1="0" x2="116" y2="109"/>
        <line x1="128" y1="0" x2="128" y2="109"/><line x1="141" y1="0" x2="141" y2="109"/>
      </g>
      <line x1="0" y1="55" x2="154" y2="55" stroke="#fff" stroke-width="0.6"/>
      <path d="M0 55 C8 50 12 46 20 44 S30 40 36 42 S44 32 52 36 S60 46 66 44 S74 40 80 40 S88 48 94 46 S100 44 104 58 S110 66 112 62 S116 48 122 46 S134 40 140 40 S150 38 154 38" fill="none" stroke="#fff" stroke-width="0.9"/>
    </svg>
  </div>
  <div class="axis-months" style="left:18px;top:184px;width:152px"><span>Jan</span><span>Feb</span><span>Mar</span><span>Apr</span><span>May</span><span>Jun</span><span>Jul</span><span>Aug</span><span>Sep</span><span>Oct</span><span>Nov</span><span>Dec</span></div>

  <div class="period-label" style="top:196px">YEAR</div>
  <div class="axis-years" style="left:16px;top:242px">2016<br>2015<br>2014</div>
  <div class="chart" style="left:32px;top:209px;width:140px;height:98px">
    <div class="chart-fill"></div>
    <svg viewBox="0 0 140 98" width="140" height="98">
      <g stroke="rgba(255,255,255,0.45)" stroke-width="0.5">
        <line x1="12" y1="0" x2="12" y2="98"/><line x1="23" y1="0" x2="23" y2="98"/><line x1="35" y1="0" x2="35" y2="98"/>
        <line x1="47" y1="0" x2="47" y2="98"/><line x1="58" y1="0" x2="58" y2="98"/><line x1="70" y1="0" x2="70" y2="98"/>
        <line x1="82" y1="0" x2="82" y2="98"/><line x1="93" y1="0" x2="93" y2="98"/><line x1="105" y1="0" x2="105" y2="98"/>
        <line x1="117" y1="0" x2="117" y2="98"/><line x1="128" y1="0" x2="128" y2="98"/>
        <line x1="0" y1="38" x2="140" y2="38"/><line x1="0" y1="47" x2="140" y2="47"/><line x1="0" y1="56" x2="140" y2="56"/>
      </g>
      <path d="M0 48 C10 44 18 30 28 34 S40 50 50 38 S62 22 72 30 S84 48 94 36 S108 28 116 36 S132 34 140 32" fill="none" stroke="#fff" stroke-width="0.8"/>
      <path d="M0 60 C12 58 20 50 30 56 S44 66 54 52 S66 44 76 56 S90 70 100 54 S118 46 126 58 S136 62 140 60" fill="none" stroke="#fff" stroke-width="0.8"/>
      <path d="M0 42 C10 52 22 62 34 50 S50 36 60 46 S72 64 84 50 S98 40 108 52 S126 70 140 72" fill="none" stroke="#fff" stroke-width="0.8"/>
    </svg>
  </div>
  <div class="axis-months" style="left:33px;top:312px;width:138px"><span>Jan</span><span>Feb</span><span>Mar</span><span>Apr</span><span>May</span><span>Jun</span><span>Jul</span><span>Aug</span><span>Sep</span><span>Oct</span><span>Nov</span><span>Dec</span></div>
</section>

<!-- Personal information -->
<section class="screen screen--profile">
  <div class="sky-clouds"></div>
  <div class="status-bar status-bar--light"><span>●●●○○ NOVA</span><span>4:21 PM</span><span>100%<i class="battery"></i></span></div>
  <header class="app-header"><span class="menu"></span><span class="prev">&lt;</span>Personal Information<span class="next">&gt;</span></header>

  <p class="profile-name">Owen Harlow</p>
  <div class="profile-photo" role="img" aria-label="Profile photo of the user"></div>
  <p class="profile-facts">Age: <b>22</b>yrs<br>Gender: <b>Male</b><br>Height: <b>6</b>ft <b>5</b>in<br>Weight: <b>149</b>lbs</p>

  <ul class="link-list">
    <li>Medications</li>
    <li>Consultations</li>
    <li>Health Check</li>
  </ul>

  <div class="section-band" style="top:164px">Friend and Family</div>
  <ul class="people-list" style="top:187px">
    <li>Emily</li>
    <li>Jackson</li>
    <li class="add">Add Profile</li>
  </ul>

  <div class="section-band" style="top:234px">Most recently consultations</div>
  <ul class="plain-list" style="top:256px">
    <li>Depression</li>
    <li>Anxiety</li>
  </ul>
</section>

<!-- Activity -->
<section class="screen screen--activity">
  <div class="sky-clouds"></div>
  <div class="status-bar"><span>●●●○○ NOVA</span><span>4:21 PM</span><span>100%<i class="battery"></i></span></div>
  <header class="app-header"><span class="menu"></span><span class="prev">&lt;</span><span class="edit-icon"></span>Activity<span class="next">&gt;</span></header>

  <div class="activity-feed">
    <h2 class="activity-title">Physical exercises</h2>
    <p class="activity-text">If you want to improve your mood try gentle exercises or go for a walk for 20 minutes</p>
    <p class="activity-date">12 Sep 2015</p>

    <h2 class="activity-title">Gain useful tips how to fight your bad mood</h2>
    <ul class="activity-tips">
      <li>Smile. It's cheesy, but apparently it's true: The act of smiling really can turn a frown upside down.</li>
      <li>Jump around. Get happy-making endorphins pumping fast with some jumping jacks, jump rope, or random flailing around (hey, no judgment here).</li>
      <li>Chew gum. The repetitive action of gnawing on gum can promote relaxation and reduce anxiety and stress.</li>
    </ul>
    <p class="activity-date">18 Sep 2015</p>

    <h2 class="activity-title">Test your mood regularly</h2>
    <p class="activity-text">Remember testing mood on a regular basis is a way to effective feedback from the app it will help you discover what makes you feel depressed and what boosts your mood</p>
    <p class="activity-date">18 Sep 2015</p>
  </div>
</section>

</body>
</html>
```